Media Services Start-up -- Corporate Website and Logo Design. Inspiration required!

We need a logo design and corporate website design, including coding, for our start-up business.
Vennatra’s value proposition is based on bringing together media content from a vast number of geographies globally, adding human and AI curation, translation and editing, and delivering the content using tailored customer interfaces. On the one hand, the business brings together media coverage from all over the world, and on the other it brings together content, human skills and technology to deliver a supreme customer experience.
Vennatra is a B2B media monitoring and analytics business with emphasis on global customers. Vennatra's service offering is centred around sourcing media content from different markets, processing, storing and delivering the content and insights derived from it using an online platform / mobile app.
The messaging we want to create through the logo is:
- Global scope
- Speed of delivery
- Cost-efficiency
- Multi-lingual
- Tailor-made
- Trustworthy
Target Market(s)
Business to business, PR / Communications, Media, Marketing
Logo Text
Vennatra
Coding
Coded - Design and coding required
Number of Pages Required
5+ page
Font styles to use
Other font styles liked:
- See Design Brief for details
Colors
Designer to choose colors to be used in the design.

```html
<!DOCTYPE html>
<html lang="en">
<head>
<meta charset="utf-8">
<title>Vennatra Media Intelligence – Our Solutions</title>
<link href="https://fonts.googleapis.com/css2?family=Roboto:wght@300;400;500;700&display=swap" rel="stylesheet">
<style>
  :root{
    --teal:#36b0a0;
    --header:#141414;
    --ink:#ffffff;
    --muted:#d9d9d9;
    --bg-deep:#050505;
  }
  *{box-sizing:border-box;margin:0;padding:0}
  html,body{width:1200px;height:776px;overflow:hidden;background:var(--bg-deep)}
  body{position:relative;font-family:"Roboto",Arial,sans-serif;color:var(--ink)}
  .abs{position:absolute}

  .hero-backdrop{left:0;top:0;width:1200px;height:741px;
    background:
      radial-gradient(ellipse 220px 200px at 600px 300px, rgba(120,120,120,.35), transparent 70%),
      radial-gradient(ellipse 700px 260px at 600px 260px, rgba(70,70,70,.55), transparent 75%),
      linear-gradient(180deg,#2a2a2a 0%,#1b1b1b 35%,#0a0a0a 75%,#000 100%);}

  .site-header{left:0;top:0;width:1200px;height:85px;background:rgba(18,18,18,.92)}
  .brand{left:141px;top:13px;display:flex;align-items:center;gap:10px}
  .brand-dot{width:40px;height:40px;border-radius:50%;background:var(--teal)}
  .brand-name{font-size:13px;font-weight:300;line-height:14.5px;letter-spacing:.2px;color:var(--ink)}

  .contact{top:12px;display:flex;align-items:center;gap:8px;font-size:14px;font-weight:400}
  .contact-icon{width:27px;height:27px;border:1.5px solid #fff;border-radius:50%;display:flex;align-items:center;justify-content:center}

  .main-nav{top:53px;font-size:15px;font-weight:400}
  .main-nav a{color:var(--ink);text-decoration:none;position:absolute;white-space:nowrap}
  .main-nav a.active{color:var(--teal);font-weight:500}
  .sign-in{left:974px;top:49px;width:85px;height:29px;background:var(--teal);color:#fff;
    font-size:15.5px;display:flex;align-items:center;justify-content:center;letter-spacing:.3px}

  .page-title{left:0;top:136px;width:1200px;text-align:center;font-size:32px;font-weight:700}
  .intro{left:170px;width:860px;text-align:center;font-size:14px;font-weight:700;line-height:20px}

  .tab{top:333px;transform:translateX(-50%);text-align:center;white-space:nowrap}
  .tab svg{display:block;margin:0 auto 4px}
  .tab span{font-size:15.5px;font-weight:400;letter-spacing:.3px}
  .tab.active span{font-weight:700}
  .tab-rule{left:162px;top:401px;width:876px;height:2px;background:#fff}
  .tab-rule-active{left:479px;top:400px;width:165px;height:3px;background:var(--teal)}

  .features{left:141px;top:438px;list-style:none}
  .features li{display:flex;align-items:center;height:34.5px;font-size:14px;font-weight:400}
  .features svg{margin-right:16px;flex:none}

  .slider-arrow{top:520px;width:33px;height:33px;border:1px solid #fff;display:flex;align-items:center;justify-content:center}

  .cta{left:508px;top:658px;width:184px;height:35px;background:var(--teal);display:flex;align-items:center;justify-content:center;font-size:15.5px;letter-spacing:.3px}

  .site-footer{left:0;top:741px;width:1200px;height:35px;background:var(--teal);display:flex;align-items:center;padding:0 141px;justify-content:space-between;font-size:13px;font-weight:300}
  .social{display:flex;gap:9px}
  .social i{width:14px;height:14px;border-radius:50%;background:#fff;display:block}
</style>
</head>
<body>
  <div class="abs hero-backdrop" role="img" aria-label="Dark city skyline at night with a person facing a glowing globe, network lines and faint technology icons in circles"></div>

  <header class="abs site-header"></header>
  <div class="abs brand">
    <div class="brand-dot"></div>
    <div class="brand-name">VENNATRA<br>MEDIA<br>INTELLIGENCE</div>
  </div>

  <div class="abs contact" style="left:733px">
    <span class="contact-icon"><svg width="13" height="13" viewBox="0 0 24 24"><path fill="#fff" d="M6.6 10.8a15 15 0 0 0 6.6 6.6l2.2-2.2a1 1 0 0 1 1-.25 11.4 11.4 0 0 0 3.6.6 1 1 0 0 1 1 1V20a1 1 0 0 1-1 1A17 17 0 0 1 3 4a1 1 0 0 1 1-1h3.5a1 1 0 0 1 1 1c0 1.25.2 2.45.6 3.6a1 1 0 0 1-.25 1z"/></svg></span>
    <span>+1 555 010 2040</span>
  </div>
  <div class="abs contact" style="left:900px">
    <span class="contact-icon"><svg width="14" height="10" viewBox="0 0 14 10"><rect x=".6" y=".6" width="12.8" height="8.8" fill="none" stroke="#fff" stroke-width="1.2"/><path d="M.6.8 7 5.6 13.4.8" fill="none" stroke="#fff" stroke-width="1.2"/></svg></span>
    <span>hello@vennatra.net</span>
  </div>

  <nav class="abs main-nav" style="left:0;width:1200px">
    <a style="left:498px">Home</a>
    <a class="active" style="left:562px">Solutions</a>
    <a style="left:647px">Our Approach</a>
    <a style="left:760px">Our People</a>
    <a style="left:856px">Our Technology</a>
  </nav>
  <div class="abs sign-in">SIGN IN</div>

  <h1 class="abs page-title">Our Solutions</h1>
  <p class="abs intro" style="top:193px">In servicing the media monitoring and PR measurement needs of global clients, we are guided by our core values to deliver Precision, Speed, Reliability, Efficiency and Premium Customer Service.</p>
  <p class="abs intro" style="top:244px">In servicing the media monitoring and PR measurement needs of global clients, we are guided by our core values to deliver Precision, Speed, Reliability, Efficiency and Premium Customer Service.</p>

  <div class="abs tab" style="left:227px">
    <svg width="32" height="32" viewBox="0 0 32 32"><circle cx="16" cy="7" r="5" fill="#fff"/><rect x="4" y="16" width="11" height="9" fill="none" stroke="#fff" stroke-width="2"/><rect x="19" y="15" width="8" height="11" fill="none" stroke="#fff" stroke-width="2"/><path d="M3 28h26" stroke="#fff" stroke-width="2"/></svg>
    <span>Content Sourcing</span>
  </div>
  <div class="abs tab" style="left:385px">
    <svg width="32" height="32" viewBox="0 0 32 32"><circle cx="16" cy="9" r="8" fill="#fff"/><circle cx="7" cy="22" r="3" fill="#fff"/><circle cx="16" cy="22" r="3" fill="#fff"/><circle cx="25" cy="22" r="3" fill="#fff"/><path d="M3 31v-3h8v3M12 31v-3h8v3M21 31v-3h8v3" fill="#fff"/></svg>
    <span>Content Collection</span>
  </div>
  <div class="abs tab active" style="left:563px">
    <svg width="32" height="32" viewBox="0 0 32 32"><path d="M3 3l26 26M29 3 3 29" stroke="var(--teal)" stroke-width="2"/><circle cx="16" cy="12" r="5" fill="var(--teal)"/><path d="M9 26c0-6 3-9 7-9s7 3 7 9z" fill="var(--teal)"/></svg>
    <span>Content Augmentation</span>
  </div>
  <div class="abs tab" style="left:732px">
    <svg width="32" height="32" viewBox="0 0 32 32"><circle cx="16" cy="16" r="8" fill="none" stroke="#fff" stroke-width="2"/><circle cx="16" cy="16" r="3" fill="#fff"/><g fill="#fff"><circle cx="16" cy="2" r="2"/><circle cx="16" cy="30" r="2"/><circle cx="2" cy="16" r="2"/><circle cx="30" cy="16" r="2"/><circle cx="6" cy="6" r="2"/><circle cx="26" cy="26" r="2"/><circle cx="26" cy="6" r="2"/><circle cx="6" cy="26" r="2"/></g></svg>
    <span>Content Delivery</span>
  </div>
  <div class="abs tab" style="left:927px">
    <svg width="36" height="32" viewBox="0 0 36 32"><ellipse cx="26" cy="8" rx="9" ry="6" fill="#fff"/><circle cx="13" cy="15" r="5" fill="#fff"/><path d="M3 30c0-6 4-9 10-9s10 3 10 9z" fill="#fff"/></svg>
    <span>Media Insights &amp; Consultancy</span>
  </div>
  <div class="abs tab-rule"></div>
  <div class="abs tab-rule-active"></div>

  <ul class="abs features">
    <li><svg width="14" height="14" viewBox="0 0 14 14"><rect x="1" y="1" width="12" height="12" rx="3" fill="none" stroke="var(--teal)" stroke-width="2"/><path d="M4 7.2l2 2 4-4.2" fill="none" stroke="var(--teal)" stroke-width="1.6"/></svg>We manage and normalise all of the source-level reference data - country, language, reach etc.</li>
    <li><svg width="14" height="14" viewBox="0 0 14 14"><rect x="1" y="1" width="12" height="12" rx="3" fill="none" stroke="var(--teal)" stroke-width="2"/><path d="M4 7.2l2 2 4-4.2" fill="none" stroke="var(--teal)" stroke-width="1.6"/></svg>We add editorial validation to ensure only the content required reaches your delivery, removing inevitable noise from source providers</li>
    <li><svg width="14" height="14" viewBox="0 0 14 14"><rect x="1" y="1" width="12" height="12" rx="3" fill="none" stroke="var(--teal)" stroke-width="2"/><path d="M4 7.2l2 2 4-4.2" fill="none" stroke="var(--teal)" stroke-width="1.6"/></svg>Tagging - AI and human based tagging to detect locations, people, topics, products, brands, services, etc.</li>
    <li><svg width="14" height="14" viewBox="0 0 14 14"><rect x="1" y="1" width="12" height="12" rx="3" fill="none" stroke="var(--teal)" stroke-width="2"/><path d="M4 7.2l2 2 4-4.2" fill="none" stroke="var(--teal)" stroke-width="1.6"/></svg>Human and automated grouping of stories across geographies - clustering, "also-in" groupings etc.</li>
    <li><svg width="14" height="14" viewBox="0 0 14 14"><rect x="1" y="1" width="12" height="12" rx="3" fill="none" stroke="var(--teal)" stroke-width="2"/><path d="M4 7.2l2 2 4-4.2" fill="none" stroke="var(--teal)" stroke-width="1.6"/></svg>Translation summarisation - AI Translation or human-created depending on budget, speed of delivery and need.</li>
    <li><svg width="14" height="14" viewBox="0 0 14 14"><rect x="1" y="1" width="12" height="12" rx="3" fill="none" stroke="var(--teal)" stroke-width="2"/><path d="M4 7.2l2 2 4-4.2" fill="none" stroke="var(--teal)" stroke-width="1.6"/></svg>Digest authoring - refining the essence of today’s coverage into a concise board-ready output for your organisation</li>
  </ul>

  <div class="abs slider-arrow" style="left:50px"><svg width="12" height="20" viewBox="0 0 12 20"><path d="M10 1 2 10l8 9" fill="none" stroke="#fff" stroke-width="1.6"/></svg></div>
  <div class="abs slider-arrow" style="left:1117px"><svg width="12" height="20" viewBox="0 0 12 20"><path d="M2 1l8 9-8 9" fill="none" stroke="#fff" stroke-width="1.6"/></svg></div>

  <div class="abs cta">CONTACT US TODAY</div>

  <footer class="abs site-footer">
    <span>Copyright © 2019 Vennatra Media Intelligence. All Rights Reserved.</span>
    <div class="social"><i></i><i></i><i></i></div>
  </footer>
</body>
</html>
```